NZ First of it's kind solutions directory and marketplace for busy Mums needs a business card design

We need a business card design for our new nationwide business in NZ (long term plans to go global). We provide solutions to the everyday challenges that busy Mums face by connecting them with quality communities and suppliers of carefully selected, relevant products and services. We sell direct via our online marketplace. The final design should communicate our values of inclusivity, quality and smart solutions. Colours should incorporate our logo colour palette of #477077 and #6ba8b2. Our website is at https://www.brightnestmums.example

Target Market(s)

busy Mums, Age 28 – 50, female, income over $100K, location main centres NZ primarily but NZ wide. Is likely juggling work or career with a young family. Probably had hobbies which have fallen by the wayside.
-Wants to succeed in her chosen career without compromising on family life
-to successfully juggle her career without feeling like she is compromising her children
- Is time poor, something always has to give and it’s generally her health (she’ll stay up late, get stressed)
- probably ex corporate or professional career. Has discretional income

Industry/Entity Type

Business

Contact Information for Business Card

Lena Forbisher, Founder, BrightNestMums.example (Strapline Tap; Gather; Sorted), 47 Kowhai Terrace, Ellerslie, Auckland 1051, New Zealand. Mob: 021 483 517 Ph: +64 (0)9 571 4860

Font styles to use
Other font styles liked:
• Raleway, and/or Architects Daughter

Colors
00a990
33b8a4
86cfc6
cfeae6

Requirements
Must have
• the above details, streamline. the logo and colours associated with those logos
Should not have
• foil or metallic colours

```html
<!DOCTYPE html>
<html lang="en">
<head>
<meta charset="utf-8">
<title>BrightNestMums – Business Card</title>
<link rel="stylesheet" href="https://fonts.googleapis.com/css2?family=Arimo:wght@400;700&display=swap">
<style>
  :root {
    --teal-deep: #477077;
    --teal-light: #6ba8b2;
    --teal-back: #4a7a82;
    --paper: #f7f7f6;
    --stage: #e6e4e0;
    --white: #ffffff;
    --grey-soft: #c9d8da;
  }
  * { box-sizing: border-box; margin: 0; padding: 0; }
  html, body {
    width: 1200px;
    height: 886px;
    overflow: hidden;
    background: var(--stage);
    font-family: "Arimo", Arial, sans-serif;
  }
  .stage {
    position: relative;
    width: 1200px;
    height: 886px;
    display: flex;
    align-items: center;
    justify-content: center;
    gap: 90px;
  }
  .card {
    position: relative;
    width: 340px;
    height: 595px;
    border-radius: 4px;
    box-shadow: 0 6px 18px rgba(0,0,0,0.18);
    overflow: hidden;
  }

  /* Front */
  .card--front { background: var(--paper); }
  .front__brand {
    position: absolute;
    top: 52px;
    left: 0;
    right: 0;
    text-align: center;
    font-weight: 700;
    font-size: 34px;
    letter-spacing: -1.2px;
    color: var(--teal-deep);
  }
  .front__panel {
    position: absolute;
    left: 34px;
    right: 34px;
    top: 160px;
    bottom: 70px;
    background: var(--teal-deep);
    border-radius: 6px;
    color: var(--white);
    padding: 110px 26px 0;
    text-align: center;
  }
  .contact__name {
    font-weight: 700;
    font-size: 19px;
    letter-spacing: 0.3px;
    text-transform: uppercase;
  }
  .contact__role {
    margin-top: 3px;
    font-size: 13px;
    letter-spacing: 1px;
    text-transform: uppercase;
    color: var(--teal-light);
  }
  .contact__address {
    margin-top: 26px;
    font-size: 13.5px;
    line-height: 1.45;
  }
  .contact__lines {
    margin-top: 20px;
    font-size: 13.5px;
    line-height: 1.5;
    list-style: none;
  }
  .contact__lines b { font-weight: 700; }

  /* Back */
  .card--back {
    background: var(--teal-back);
    display: flex;
    align-items: center;
    justify-content: center;
  }
  .back__brand {
    display: flex;
    align-items: center;
    gap: 14px;
    transform: rotate(90deg);
    white-space: nowrap;
  }
  .back__dot {
    width: 26px;
    height: 26px;
    border-radius: 50%;
    background: var(--white);
  }
  .back__name {
    font-weight: 700;
    font-size: 38px;
    letter-spacing: -1.2px;
    color: var(--white);
  }
</style>
</head>
<body>
  <main class="stage">
    <section class="card card--front" aria-label="Business card front">
      <div class="front__brand">BrightNestMums</div>
      <div class="front__panel">
        <p class="contact__name">Lena Forbisher</p>
        <p class="contact__role">Founder</p>
        <p class="contact__address">47 Kowhai Terrace, Ellerslie<br>Auckland 1051, New Zealand.</p>
        <ul class="contact__lines">
          <li><b>P:</b> +64 (0)9 571 4860</li>
          <li><b>M:</b> 021 483 517</li>
          <li><b>W:</b> BrightNestMums.example</li>
        </ul>
      </div>
    </section>

    <section class="card card--back" aria-label="Business card back">
      <div class="back__brand">
        <span class="back__dot"></span>
        <span class="back__name">BrightNestMums</span>
      </div>
    </section>
  </main>
</body>
</html>
```